ByteLotus.com Redesign

Please read the notes and see the site-map attached.
Updates

We are looking for something highly creative. Please provide your best work. Best of luck and thank you very much for your hard work!

Project Deadline Extended
Reason: I am seeing good designs but I am not seeing great designs. I really need a design that is unique and is going to wow me. No one is required to stick to the existing color schemes etc. You are free to use other colors etc. I am seeing a lot of the same colors that are used on the site now.

Target Market(s)

Business and entrepreneurs mainly. People looking to build applications, software or launch web or mobile tech products.

Colors

Designer to choose colors to be used in the design.

Requirements
Must have
• See my attached html file.
Nice to have
Should not have
• No sure

```html
<!DOCTYPE html>
<html lang="en">
<head>
<meta charset="utf-8">
<title>ByteLotus.com</title>
<link rel="stylesheet" href="https://fonts.googleapis.com/css2?family=Roboto+Condensed:wght@400;700&family=Roboto:wght@400;500&family=Jura:wght@400&family=Dosis:wght@400;500&display=swap">
<style>
:root{
  --green:#6cbf2c;
  --green-dark:#4fa519;
  --navy:#1f3049;
  --navy-footer:#1f324d;
  --text:#333;
  --muted:#555;
  --hero-top:#fdfdfd;
  --hero-bottom:#dedede;
  --white:#fff;
  --accent-red:#e8474b;
  --chat-orange:#f28a0c;
}
*{margin:0;padding:0;box-sizing:border-box}
html,body{width:757px;height:1200px;overflow:hidden;background:var(--white)}
body{position:relative;font-family:"Roboto",sans-serif;color:var(--text)}
.abs{position:absolute}
.top-rule{left:0;top:0;width:757px;height:3px;background:var(--green)}
.hero{left:0;top:3px;width:757px;height:332px;background:radial-gradient(circle at 55% 40%,var(--hero-top),var(--hero-bottom) 90%)}
.hero-art{left:296px;top:62px;width:330px;height:244px;border-radius:50% 50% 0 0;background:radial-gradient(circle at 45% 60%,#d3ebc0,#e8f2df 55%,rgba(232,232,232,0) 78%)}
.hero-bubble{border-radius:50%;background:radial-gradient(circle at 40% 40%,#fff,#e4e4e4)}
.brand{left:108px;top:20px;display:flex;align-items:center;gap:8px;font-family:"Roboto Condensed",sans-serif;font-weight:700;font-size:25px;color:var(--navy)}
.brand-dot{width:32px;height:32px;border-radius:50%;background:var(--navy)}
.phone{left:560px;top:10px;display:flex;align-items:center;gap:6px;font-family:"Roboto Condensed",sans-serif;font-size:13px;color:var(--navy)}
.account{left:475px;top:45px;font-size:9px;color:var(--navy)}
.quote-btn{left:551px;top:40px;width:68px;height:20px;border:1px solid var(--green);border-radius:3px;font-size:9px;color:var(--navy);display:flex;align-items:center;justify-content:center;background:var(--white)}
.menu{left:632px;top:42px;width:16px}
.menu span{display:block;height:2px;background:var(--navy);margin-bottom:3px}
.hire{left:703px;top:38px;height:20px;border-left:3px solid var(--green);padding-left:12px;font-size:9px;color:var(--navy);line-height:20px}
.headline{left:110px;top:111px;font-family:"Roboto Condensed",sans-serif;font-weight:700;font-size:22.5px;line-height:23px;color:var(--navy);text-transform:uppercase}
.detail-btn{left:108px;top:216px;width:134px;height:22px;background:var(--green);color:var(--white);font-size:8.5px;font-weight:500;display:flex;align-items:center;justify-content:center;gap:5px;border-radius:2px}
.slider-dots{left:727px;top:165px}
.slider-dots i{display:block;width:6px;height:6px;border-radius:50%;background:#ccc;margin-bottom:4px}
.slider-dots i.on{background:var(--green)}
.features{left:111px;top:306px;display:flex;gap:12px}
.feature{width:79px;text-align:center;font-size:8.5px;line-height:10px;color:var(--text)}
.feature-card{height:56px;background:var(--white);box-shadow:0 1px 4px rgba(0,0,0,.18);display:flex;align-items:center;justify-content:center;margin-bottom:6px}
.feature-icon{width:36px;height:36px;border-radius:6px}
.title-row{left:0;width:757px;display:flex;align-items:center;font-family:"Jura",sans-serif;font-size:16px;letter-spacing:1.5px;color:var(--navy);line-height:18px}
.title-row .rule{height:1px;background:var(--green)}
.title-row .grow{flex:1}
.title-row span{padding:0 12px;white-space:nowrap}
.intro{left:128px;top:459px;width:502px;text-align:center;font-size:7.8px;line-height:12px;color:var(--muted)}
.ghost-btn{height:20px;border:1px solid #444;border-radius:3px;font-size:8px;display:flex;align-items:center;justify-content:center;background:var(--white);color:var(--text)}
.skill{position:absolute;top:608px;width:110px;text-align:center;font-size:9.5px;color:var(--text)}
.skill-ring{width:62px;height:62px;margin:0 auto 6px;border:2px solid var(--green);border-radius:50%;display:flex;align-items:center;justify-content:center}
.laptop{left:102px;top:772px;width:302px;height:164px;background:linear-gradient(#c7c7c7,#8f8f8f);border-radius:10px 10px 4px 4px}
.avatar{left:481px;top:760px;width:64px;height:64px;border-radius:50%;border:3px solid var(--green);background:radial-gradient(circle at 50% 45%,#e8c8a8,#8a6445)}
.testimonial{left:416px;top:828px;width:194px;text-align:center;font-size:8.5px;line-height:12px;color:var(--text)}
.testimonial b{font-weight:400;color:var(--accent-red)}
.t-dots{left:496px;top:919px;display:flex;gap:3px}
.t-dots i{width:6px;height:6px;border-radius:50%;background:#ddd}
.t-dots i.on{background:var(--green)}
.chat{left:522px;top:955px;width:112px}
.chat-bubble{height:37px;background:var(--chat-orange);border-radius:8px;padding:5px 8px;color:var(--white)}
.chat-bubble strong{display:block;font-size:10px}
.chat-bubble small{display:block;font-size:5px;text-align:right}
.chat-bar{height:25px;background:#eee;font-size:6px;padding:12px 6px 0;color:#444}
.follow{left:0;top:1017px;width:757px;height:41px;background:var(--green);color:var(--white)}
.follow-label{position:absolute;left:110px;top:11px;font-size:12px;font-weight:500}
.social{position:absolute;top:8px;display:flex;align-items:center;gap:8px;font-size:9px}
.social i{width:25px;height:25px;border-radius:50%;background:var(--white)}
.footer{left:0;top:1058px;width:757px;height:142px;background:var(--navy-footer);color:var(--white);font-family:"Dosis",sans-serif;font-size:8.5px}
.footer ul{position:absolute;list-style:none}
.footer li{height:17.5px}
.footer .soc li{display:flex;align-items:center;gap:5px;height:24px}
.footer .soc i{width:14px;height:14px;border-radius:50%}
.news-title{position:absolute;left:498px;top:21px;font-size:10px;font-weight:500}
.news-box{position:absolute;left:498px;top:39px;width:150px;height:25px;background:var(--green-dark);font-size:10px;padding:6px}
.copy{position:absolute;left:0;top:118px;width:757px;text-align:center;font-size:8px}
</style>
</head>
<body>
<div class="abs top-rule"></div>

<section class="abs hero"></section>
<div class="abs hero-bubble" style="left:165px;top:182px;width:105px;height:105px"></div>
<div class="abs hero-bubble" style="left:508px;top:58px;width:90px;height:90px"></div>
<div class="abs hero-bubble" style="left:705px;top:205px;width:60px;height:60px"></div>
<div class="abs hero-art" role="img" aria-label="Hero illustration: a smartphone with a tick inside a ring, beside a cartoon mascot"></div>

<div class="abs brand"><i class="brand-dot"></i>bytelotus</div>
<div class="abs phone">
  <svg width="18" height="16" viewBox="0 0 18 16"><path d="M3 1 l3 0 l1 4 l-2 1 q1 3 4 5 l1 -2 l4 1 l0 3 q-8 1 -11 -12z" fill="var(--green)"/></svg>
  877 555 0142
</div>
<div class="abs account">Login &nbsp;|&nbsp; Register</div>
<div class="abs quote-btn">Get a Quote</div>
<div class="abs menu"><span></span><span></span><span></span></div>
<div class="abs hire">Hire Us !</div>

<h1 class="abs headline">Providing better<br>solutions<br>for your online<br>presence</h1>
<div class="abs detail-btn">Click here for more detail
  <svg width="10" height="10" viewBox="0 0 10 10"><circle cx="5" cy="5" r="5" fill="#fff"/><path d="M3 5h4M5 3l2 2-2 2" stroke="var(--green)" fill="none" stroke-width="1.3"/></svg>
</div>
<div class="abs slider-dots"><i></i><i class="on"></i></div>

<div class="abs features">
  <div class="feature"><div class="feature-card"><div class="feature-icon" role="img" aria-label="Touch screen icon" style="background:#5bb8e0"></div></div>Intuitive<br>UI</div>
  <div class="feature"><div class="feature-card"><div class="feature-icon" role="img" aria-label="Robot icon" style="background:#6cbf2c"></div></div>Robust<br>Engineering</div>
  <div class="feature"><div class="feature-card"><div class="feature-icon" role="img" aria-label="Tags icon" style="background:#1f3049"></div></div>Unified Aesthetic<br>Designs</div>
  <div class="feature"><div class="feature-card"><div class="feature-icon" role="img" aria-label="Devices icon" style="background:#f0a040"></div></div>Multiple Device<br>Compatibility</div>
  <div class="feature"><div class="feature-card"><div class="feature-icon" role="img" aria-label="Coin stack icon" style="background:#9b7fe0"></div></div><span style="font-size:7.6px">Cost Effective<br>solution</span></div>
  <div class="feature"><div class="feature-card"><div class="feature-icon" role="img" aria-label="Mobile phone icon" style="background:#e53030"></div></div><span style="font-size:7.6px">Transparent<br>Communication</span></div>
</div>

<h2 class="abs title-row" style="top:430px"><i class="rule grow"></i><span>WELCOME TO BYTE LOTUS</span><i class="rule grow"></i></h2>
<p class="abs intro">Praesent ipsum nisi, dapibus tempus sodales quis, vehicula suscipit nulla. Etiam dictum lacus non lacus pharetra viverra. Donec dignissim sed lorem a pulvinar. Praesent varius odio pellentesque vulputate mattis. Morbi nec adipiscing dui. Nam faucibus placerat odio, a rutrum urna venenatis id. In in laoreet urna.</p>
<div class="abs ghost-btn" style="left:349px;top:510px;width:62px">View more »</div>

<h2 class="abs title-row" style="top:566px"><i class="rule" style="width:316px"></i><span>OUR SKILLS</span><i class="rule grow"></i></h2>
<div class="abs ghost-btn" style="left:550px;top:566px;width:55px;border-color:var(--green)">View more »</div>

<div class="skill" style="left:119px"><div class="skill-ring"><svg width="22" height="22" viewBox="0 0 22 22"><circle cx="11" cy="11" r="6" fill="none" stroke="var(--navy)" stroke-width="4" stroke-dasharray="3 2"/></svg></div>Web Development</div>
<div class="skill" style="left:253px"><div class="skill-ring"><svg width="22" height="22" viewBox="0 0 22 22"><path d="M3 20V14M8 20V11M13 20V8M18 20V5" stroke="var(--navy)" stroke-width="3"/><path d="M3 10l15-8" stroke="var(--navy)" stroke-width="1.5"/></svg></div>SEO</div>
<div class="skill" style="left:383px"><div class="skill-ring"><svg width="22" height="22" viewBox="0 0 22 22"><path d="M3 19L19 3M3 3l16 16" stroke="var(--navy)" stroke-width="3"/></svg></div>Graphic Design</div>
<div class="skill" style="left:517px"><div class="skill-ring"><svg width="22" height="22" viewBox="0 0 22 22"><rect x="3" y="5" width="10" height="12" rx="2" fill="var(--navy)"/><path d="M9 11h10M15 7l4 4-4 4" stroke="var(--navy)" stroke-width="2.5" fill="none"/></svg></div>Outsourcing</div>

<h2 class="abs title-row" style="top:721px"><i class="rule" style="width:193px"></i><span>VIDEO TOUR</span><i class="rule grow"></i><span>TESTIMONIALS</span><i class="rule" style="width:169px"></i></h2>

<div class="abs laptop" role="img" aria-label="Laptop showing a video preview of the website"></div>
<svg class="abs" style="left:240px;top:832px" width="32" height="34" viewBox="0 0 32 34" aria-hidden="true"><path d="M2 1L30 17L2 33Z" fill="#fff"/></svg>

<div class="abs avatar" role="img" aria-label="Portrait photo of the client giving the testimonial"></div>
<p class="abs testimonial">“ Lorem ipsum dolor sit amet, consectetur adipisicing elit. Facilis minus pariatur eligendi sunt doloremque vitae reiciendis tempore voluptatibus quis architecto suscipit magnam. Lorem ipsum dolor sit amet, consectetur adipisicing elit. Facilis minus pariatur eligendi. - <b>Rina Solano</b> ”</p>
<div class="abs t-dots"><i class="on"></i><i></i><i></i></div>

<div class="abs chat">
  <div class="chat-bubble"><strong>Questions?</strong><small>Click here to chat with us!</small></div>
  <div class="chat-bar">Offline - Leave a message</div>
</div>

<div class="abs follow">
  <span class="follow-label">Follow us at:</span>
  <div class="social" style="left:271px"><i></i>Facenet</div>
  <div class="social" style="left:371px"><i></i>Chirper</div>
  <div class="social" style="left:467px"><i></i>Linkwork</div>
  <div class="social" style="left:564px"><i></i>Orbit plus</div>
</div>

<footer class="abs footer">
  <ul style="left:109px;top:22px"><li>Home</li><li>About Us</li><li>Our Work</li><li>Services</li><li>Reach Us</li></ul>
  <ul style="left:204px;top:22px"><li>Web Development</li><li>Mobile App Development</li><li>Custom Software Development</li><li>User Experience Design</li></ul>
  <ul class="soc" style="left:354px;top:16px">
    <li><i style="background:#3b5b9a"></i>Facenet</li>
    <li><i style="background:#3fa0d8"></i>Chirper</li>
    <li><i style="background:#d94a38"></i>Orbit Plus</li>
  </ul>
  <div class="news-title">Subscribe Your Newsletter</div>
  <div class="news-box">NEWSLETTER
    <svg style="position:absolute;right:8px;top:5px" width="20" height="14" viewBox="0 0 20 14"><rect x="1" y="1" width="18" height="12" fill="none" stroke="#fff"/><path d="M1 1l9 7 9-7" fill="none" stroke="#fff"/></svg>
  </div>
  <div class="copy">Copyrights © 2014. ByteLotus LLC. Privacy Policy</div>
</footer>
</body>
</html>
```